Business Cards Needed for Innovative Healthcare Marketing Company

We are a marketing company focused on healthcare. Our company is all about rebranding yourself renewing your image and generating results. The phoenix stands for "reborn" or "rising" which we provide new brands for our clients we take their old brands and renew it with creativity and innovation. I am looking for a business card with color dimension. I have attached an example of a card I think has the look and feel of what I am trying to accomplish. I like that the card example has black and grey font colors, I like the font placement and the small logo, I really like the use of the colors on the right those are the colors of my logo. My logo is phoenix so maybe incorporating flames similar to that design. I would like the back a solid color maybe red with an opaque version of the logo and website. As a marketing company I am always open to creative liberty!

Target Market(s)

Doctors and business professionals.

Industry/Entity Type

Marketing

Contact Information for Business Card

Valcorne Health Care Marketing
Marla Tenwick- CEO
#(512)638-2974
email-marla@valcorne.com
website- valcorne.com

Font styles to use
Sans Serif

Colors
ec1f27
f37122
ffc214
fbed22
fbf289
f04a50

Requirements
Must have
• The logo and required information
Nice to have
• icons by the information
Should not have
• child like font

```html
<!DOCTYPE html>
<html lang="en">
<head>
<meta charset="UTF-8">
<title>Valcorne Health Care Marketing – Business Cards</title>
<link href="https://fonts.googleapis.com/css2?family=Montserrat:wght@300;400;500;700&display=swap" rel="stylesheet">
<style>
  :root {
    --stage: #2e2e2e;
    --orange: #f7981f;
    --red: #a8202a;
    --white: #ffffff;
    --text-red: #a8202a;
  }
  * { box-sizing: border-box; margin: 0; padding: 0; }
  html, body { width: 1200px; height: 900px; overflow: hidden; }
  body {
    background: var(--stage);
    font-family: "Montserrat", Arial, sans-serif;
    position: relative;
  }
  .card {
    position: absolute;
    width: 620px;
    height: 354px;
    border-radius: 22px;
    overflow: hidden;
    box-shadow: 0 14px 30px rgba(0,0,0,0.45);
  }

  /* Back side */
  .card-back { left: 90px; top: 70px; background: var(--orange); }
  .card-back .brand-mark {
    position: absolute; left: 0; right: 0; top: 130px;
    text-align: center;
    color: var(--white);
    font-size: 40px; font-weight: 400; letter-spacing: 4px;
    display: flex; align-items: center; justify-content: center; gap: 14px;
  }
  .card-back .brand-mark .dot {
    width: 18px; height: 18px; border-radius: 50%; background: var(--white);
  }
  .card-back .website {
    position: absolute; left: 312px; bottom: 26px;
    color: var(--white); font-size: 15px; letter-spacing: 0.5px;
  }
  .card-back .edge { position: absolute; bottom: 0; height: 13px; }
  .card-back .edge-red { left: 0; width: 60%; background: var(--red); }
  .card-back .edge-white { right: 0; width: 40%; background: var(--white); }

  /* Front side */
  .card-front { left: 490px; top: 476px; background: var(--white); }
  .logo {
    position: absolute; left: 40px; top: 60px;
    display: flex; align-items: center; gap: 14px;
    color: var(--text-red); font-weight: 300;
  }
  .logo .dot { width: 22px; height: 22px; border-radius: 50%; background: var(--orange); }
  .logo .name { font-size: 34px; letter-spacing: 2px; line-height: 1; }
  .logo .tagline { font-size: 13px; letter-spacing: 1.5px; margin-top: 6px; padding-top: 5px; border-top: 1px solid var(--text-red); }

  .person {
    position: absolute; right: 36px; top: 58px; text-align: right;
  }
  .person .full-name { color: var(--orange); font-weight: 700; font-size: 22px; letter-spacing: 0.5px; }
  .person .role { color: var(--text-red); font-size: 12px; font-weight: 500; }
  .person-rule {
    position: absolute; right: 30px; top: 122px; width: 380px; height: 2px; background: var(--text-red);
  }

  .contact-rule {
    position: absolute; left: 40px; top: 232px; width: 250px; height: 2px; background: var(--text-red);
  }
  .contacts { position: absolute; left: 40px; top: 242px; list-style: none; }
  .contacts li {
    display: flex; align-items: center; gap: 10px;
    color: var(--text-red); font-size: 15px; line-height: 22px;
  }
  .contacts svg { width: 12px; height: 12px; fill: none; stroke: var(--orange); stroke-width: 2; }

  .card-front .edge { position: absolute; bottom: 0; height: 13px; }
  .card-front .edge-orange { left: 0; width: 62%; background: var(--orange); }
  .card-front .edge-red { right: 0; width: 38%; background: var(--red); }
</style>
</head>
<body>

  <section class="card card-back">
    <div class="brand-mark"><span class="dot"></span>VALCORNE</div>
    <div class="website">www.valcorne.com</div>
    <div class="edge edge-red"></div>
    <div class="edge edge-white"></div>
  </section>

  <section class="card card-front">
    <div class="logo">
      <span class="dot"></span>
      <div>
        <div class="name">VALCORNE</div>
        <div class="tagline">HEALTH CARE MARKETING</div>
      </div>
    </div>

    <div class="person">
      <div class="full-name">MARLA TENWICK</div>
      <div class="role">CEO</div>
    </div>
    <div class="person-rule"></div>

    <div class="contact-rule"></div>
    <ul class="contacts">
      <li>
        <svg viewBox="0 0 12 12"><path d="M2 1 L4 1 L5 4 L3.5 5 Q5 8 7 8.5 L8 7 L11 8 L11 10 Q6 12 2 6 Q1 3 2 1 Z"/></svg>
        (512)638-2974
      </li>
      <li>
        <svg viewBox="0 0 12 12"><rect x="1" y="2.5" width="10" height="7"/><path d="M1 2.5 L6 6.5 L11 2.5"/></svg>
        marla@valcorne.com
      </li>
      <li>
        <svg viewBox="0 0 12 12"><circle cx="6" cy="6" r="5"/><path d="M1 6 H11 M6 1 Q3 6 6 11 Q9 6 6 1"/></svg>
        www.valcorne.com
      </li>
    </ul>

    <div class="edge edge-orange"></div>
    <div class="edge edge-red"></div>
  </section>

</body>
</html>
```